Business Card & Letterhead Design

We a financial advice company based in Australia. We provide advice to wealthy farmers.

We are changing our business name FROM Brightvale Financial TO Tallowmere Wealth and we need a new letterhead and double sided business card design

Attached is designs from our previous branding (Brightvale Financial) as it includes all the details we require on the new Tallowmere Wealth business cards and letterhead.

Need extra days to review

```html
<!DOCTYPE html>
<html lang="en">
<head>
<meta charset="utf-8">
<title>Tallowmere Wealth – Stationery</title>
<link rel="stylesheet" href="https://fonts.googleapis.com/css2?family=Cinzel:wght@400&family=Montserrat:wght@400&family=Roboto:wght@400&family=PT+Serif:wght@700&display=swap">
<style>
  :root{
    --backdrop:#999999;
    --paper:#f7f7f5;
    --ink:#3f3f3f;
    --ink-soft:#555555;
    --card-dark:#3f3f3f;
    --card-ghost:#4a4a4a;
    --stripe:#7a7a7a;
    --watermark:#ececec;
    --white:#ffffff;
  }
  *{box-sizing:border-box;margin:0;padding:0}
  html,body{width:1200px;height:1032px;overflow:hidden;background:var(--backdrop)}
  .canvas{position:relative;width:1200px;height:1032px}
  .wordmark{font-family:"Cinzel",serif;font-weight:400;white-space:nowrap;text-align:center}
  .tagline{font-family:"Montserrat",sans-serif;text-transform:uppercase;white-space:nowrap;text-align:center}
  .contact{font-family:"Roboto",sans-serif;text-align:right;white-space:nowrap}
  svg.icon{display:inline-block;vertical-align:middle;fill:currentColor}

  /* Letterhead */
  .letterhead{position:absolute;left:446px;top:74px;width:626px;height:884px;background:var(--paper)}
  .letterhead .brand-ring{position:absolute;left:90px;top:40px;width:76px;height:76px;border:3px solid var(--ink);border-radius:50%}
  .letterhead .wordmark{position:absolute;left:0;width:256px;top:124px;font-size:15px;color:var(--ink)}
  .letterhead .tagline{position:absolute;left:0;width:256px;top:142px;font-size:6.4px;letter-spacing:2.3px;color:var(--ink-soft)}
  .letterhead .contact-list{position:absolute;right:50px;top:50px;list-style:none}
  .letterhead .contact-list li{font-size:10.6px;line-height:14.5px;color:var(--ink)}
  .letterhead .contact-list .icon{width:9px;height:9px;margin-left:9px;color:var(--ink-soft)}
  .letterhead .watermark-ring{position:absolute;left:118px;top:244px;width:392px;height:392px;border:6px solid var(--watermark);border-radius:50%}

  /* Business card front */
  .card{position:absolute;width:271px;height:164px;overflow:hidden}
  .card-front{left:127px;top:330px;background:var(--card-dark)}
  .card-front .ghost-ring{position:absolute;left:148px;top:-4px;width:146px;height:146px;border:4px solid var(--card-ghost);border-radius:50%}
  .card-front .brand-ring{position:absolute;left:114px;top:49px;width:42px;height:42px;border:2px solid var(--white);border-radius:50%}
  .card-front .wordmark{position:absolute;left:0;width:271px;top:97px;font-size:13.5px;color:var(--white)}
  .card-front .tagline{position:absolute;left:0;width:271px;top:112px;font-size:5.8px;letter-spacing:2px;color:#dddddd}

  /* Business card back */
  .card-back{left:127px;top:537px;background:var(--paper)}
  .card-back .swoosh{position:absolute;left:0;top:0}
  .card-back .holder{position:absolute;right:14px;top:9px;text-align:right;color:var(--white)}
  .card-back .holder-name{font-family:"PT Serif",serif;font-weight:700;font-size:9.5px;letter-spacing:.3px}
  .card-back .holder-role{font-family:"Roboto",sans-serif;font-size:5.4px;line-height:7px}
  .card-back .brand-ring{position:absolute;left:48px;top:40px;width:52px;height:52px;border:2.5px solid var(--ink);border-radius:50%}
  .card-back .wordmark{position:absolute;left:0;width:148px;top:97px;font-size:11.5px;color:var(--ink)}
  .card-back .tagline{position:absolute;left:0;width:148px;top:110px;font-size:4.6px;letter-spacing:1.5px;color:var(--ink-soft)}
  .card-back .contact-list{position:absolute;right:22px;top:87px;list-style:none}
  .card-back .contact-list li{font-size:5.8px;line-height:9.3px;color:var(--ink)}
  .card-back .contact-list .icon{width:5.5px;height:5.5px;margin-left:5px;color:var(--ink-soft)}
  .card-back .online-list{position:absolute;left:14px;top:134px;list-style:none}
  .card-back .online-list li{font-family:"Roboto",sans-serif;font-size:5.8px;line-height:9.3px;color:var(--ink);white-space:nowrap}
  .card-back .online-list .icon{width:5px;height:5px;margin-right:6px;color:var(--ink-soft)}
</style>
</head>
<body>
<svg width="0" height="0" style="position:absolute" aria-hidden="true">
  <defs>
    <symbol id="i-phone" viewBox="0 0 10 10"><path d="M1 3.2C1 2 2.5 1.4 5 1.4S9 2 9 3.2V4H7V3.2H3V4H1Z M2.5 5h5l1 3.5h-7Z"/></symbol>
    <symbol id="i-mobile" viewBox="0 0 10 10"><path d="M3 0.5h4a1 1 0 0 1 1 1v7a1 1 0 0 1-1 1H3a1 1 0 0 1-1-1v-7a1 1 0 0 1 1-1Zm0.3 1.2v5.8h3.4V1.7Z"/></symbol>
    <symbol id="i-fax" viewBox="0 0 10 10"><path d="M3 0.8h4v2.4H3Z M1 3.6h8v4H7.5V6h-5v1.6H1Z M3 6.6h4v2.6H3Z"/></symbol>
    <symbol id="i-mail" viewBox="0 0 10 10"><path d="M0.8 2.2h8.4v5.6H0.8Z"/><path d="M0.8 2.2 5 5.6 9.2 2.2" fill="none" stroke="#fff" stroke-width=".7"/></symbol>
    <symbol id="i-globe" viewBox="0 0 10 10"><circle cx="5" cy="5" r="4.2"/><path d="M0.8 5h8.4M5 0.8c-2 2.5-2 5.9 0 8.4M5 0.8c2 2.5 2 5.9 0 8.4" fill="none" stroke="#fff" stroke-width=".6"/></symbol>
    <symbol id="i-pin" viewBox="0 0 10 10"><path d="M5 0.5a3.3 3.3 0 0 1 3.3 3.3C8.3 6 5 9.5 5 9.5S1.7 6 1.7 3.8A3.3 3.3 0 0 1 5 0.5Zm0 2a1.3 1.3 0 1 0 0 2.6 1.3 1.3 0 0 0 0-2.6Z"/></symbol>
  </defs>
</svg>

<main class="canvas">
  <section class="card card-front" aria-label="Business card front">
    <div class="ghost-ring"></div>
    <div class="brand-ring"></div>
    <p class="wordmark">TALLOWMERE WEALTH</p>
    <p class="tagline">Strategic Financial Advice</p>
  </section>

  <section class="card card-back" aria-label="Business card back">
    <svg class="swoosh" width="271" height="164" viewBox="0 0 271 164" aria-hidden="true">
      <path d="M0 0H271V56C205 40 140 22 75 20C42 19 18 24 0 32Z" fill="#3f3f3f"/>
      <path d="M0 40C60 22 170 38 271 66V74C170 50 80 34 0 48Z" fill="#7a7a7a"/>
      <path d="M22 26C80 10 170 22 258 48" fill="none" stroke="#f7f7f5" stroke-width="2.2" stroke-linecap="round"/>
    </svg>
    <div class="holder">
      <p class="holder-name">TOM HADLEY</p>
      <p class="holder-role">B.Ag.Sc. Dip Fin. Adv.</p>
      <p class="holder-role">Managing Director</p>
    </div>
    <div class="brand-ring"></div>
    <p class="wordmark">TALLOWMERE WEALTH</p>
    <p class="tagline">Strategic Financial Advice</p>
    <ul class="contact-list contact">
      <li>(07) 3555 0142<svg class="icon"><use href="#i-phone"/></svg></li>
      <li>(07) 3555 0198<svg class="icon"><use href="#i-mobile"/></svg></li>
      <li>0400 555 217<svg class="icon"><use href="#i-fax"/></svg></li>
      <li>Suite 8A, 14 Wattle St<svg class="icon"><use href="#i-pin"/></svg></li>
      <li>Hillcrest QLD 4000<svg class="icon" style="visibility:hidden"><use href="#i-pin"/></svg></li>
      <li>PO Box 4410<svg class="icon"><use href="#i-pin"/></svg></li>
      <li>Riverbend QLD 4000<svg class="icon" style="visibility:hidden"><use href="#i-pin"/></svg></li>
    </ul>
    <ul class="online-list">
      <li><svg class="icon"><use href="#i-mail"/></svg>tom@brightvalefinancial.com.au</li>
      <li><svg class="icon"><use href="#i-globe"/></svg>www.brightvalefinancial.com.au</li>
    </ul>
  </section>

  <section class="letterhead" aria-label="Letterhead">
    <div class="watermark-ring"></div>
    <div class="brand-ring"></div>
    <p class="wordmark">TALLOWMERE WEALTH</p>
    <p class="tagline">Strategic Financial Advice</p>
    <ul class="contact-list contact">
      <li>(07) 3555 0142<svg class="icon"><use href="#i-phone"/></svg></li>
      <li>(07) 3555 0198<svg class="icon"><use href="#i-mobile"/></svg></li>
      <li>0400 555 217<svg class="icon"><use href="#i-fax"/></svg></li>
      <li>tom@brightvalefinancial.com.au<svg class="icon"><use href="#i-mail"/></svg></li>
      <li>www.brightvalefinancial.com.au<svg class="icon"><use href="#i-globe"/></svg></li>
      <li>PO Box 4410 Riverbend QLD 4000<svg class="icon"><use href="#i-pin"/></svg></li>
      <li>Suite 8A, 14 Wattle St Hillcrest QLD 4000<svg class="icon"><use href="#i-pin"/></svg></li>
    </ul>
  </section>
</main>
</body>
</html>
```